Elevating our current Business Card Design

We want to elevate our current business card with a new design to look like a zenith 300 company. We are a premium lubricant distributor (oil and grease).
We need 2 versions, version 1 is as per the uploaded a copy of our current business card with the English version.
For our Chinese version we need to use the front to be English in English and have the back of the card designed exactly like the front for all info to be in Chinese.
The design template needs to be such that we can amend the template with adding different information for each person's card.
The background colour of the card can be changed- we just need to clearly see all information on the card and logos.
The QJR and Ember steady logos cannot have any colour or display changes- only use the logos attached.
All logos need to be included and all information from the attached current card

```html
<!DOCTYPE html>
<html lang="en">
<head>
<meta charset="utf-8">
<title>Meridian Business Card</title>
<link rel="stylesheet" href="https://fonts.googleapis.com/css2?family=Open+Sans:wght@400;600;700;800&family=Baloo+2:wght@700&display=swap">
<style>
  :root {
    --stage: #232324;
    --card: #1f1f21;
    --red: #e8262a;
    --gold: #f1b52e;
    --white: #ffffff;
    --badge: #f07a1e;
    --badge-ring: #8b8b8e;
    --ghost: #141415;
  }
  * { box-sizing: border-box; margin: 0; padding: 0; }
  html, body { width: 1200px; height: 780px; overflow: hidden; background: var(--stage); }
  body { position: relative; font-family: "Open Sans", Arial, sans-serif; color: var(--white); }

  .card {
    position: absolute; width: 580px; height: 340px;
    background: var(--card); border-radius: 22px;
    border-bottom: 4px solid var(--red); border-left: 2px solid var(--red);
    box-shadow: 0 18px 40px rgba(0,0,0,.55);
    overflow: hidden;
  }
  .card--front { left: 60px; top: 40px; }
  .card--back { left: 560px; top: 400px; }

  .brand { display: flex; align-items: center; gap: 14px; position: absolute; }
  .brand__dot { border-radius: 50%; background: var(--gold); flex: none; }
  .brand__name { font-weight: 800; color: var(--red); letter-spacing: 2px; line-height: 1; white-space: nowrap; }

  .card--front .brand { left: 0; right: 0; top: 90px; justify-content: center; }
  .card--front .brand__dot { width: 48px; height: 48px; }
  .card--front .brand__name { font-size: 58px; }

  .partner-row {
    position: absolute; left: 26px; right: 26px; bottom: 28px;
    display: flex; align-items: center; gap: 12px;
  }
  .ember { display: flex; align-items: center; gap: 6px; }
  .ember__mark { width: 22px; height: 22px; border-radius: 50%; background: var(--white); flex: none; }
  .ember__name { font-size: 12px; font-weight: 700; color: var(--white); line-height: 1.1; }
  .cert-badge { width: 36px; height: 36px; border-radius: 50%; background: var(--badge); border: 4px solid var(--badge-ring); flex: none; }

  .distributor-strip {
    display: flex; align-items: stretch; border: 2px solid var(--red); height: 46px; flex: 1;
  }
  .distributor-strip__own { display: flex; align-items: center; gap: 8px; padding: 0 10px; }
  .distributor-strip__own .brand__dot { width: 12px; height: 12px; }
  .distributor-strip__own .brand__name { font-size: 14px; letter-spacing: 1px; }
  .distributor-strip__tag { font-size: 7.5px; color: var(--red); text-transform: uppercase; line-height: 1.15; }
  .distributor-strip__partner {
    background: var(--red); color: var(--card); display: flex; flex-direction: column;
    justify-content: center; padding: 0 12px; margin-left: auto;
  }
  .partner-name { font-size: 15px; font-weight: 800; letter-spacing: 1px; line-height: 1; }
  .partner-sub { font-size: 7px; font-weight: 600; letter-spacing: 1px; text-transform: uppercase; }

  .card--back .brand { left: 30px; top: 40px; }
  .card--back .brand__dot { width: 30px; height: 30px; }
  .card--back .brand__name { font-size: 36px; }

  .ghost-brand {
    position: absolute; right: 26px; top: 108px;
    font-size: 54px; font-weight: 800; color: var(--ghost);
    letter-spacing: 2px; line-height: 1; white-space: nowrap;
  }

  .person { position: absolute; right: 40px; top: 34px; text-align: left; }
  .person__name { font-family: "Baloo 2", "Open Sans", sans-serif; font-weight: 700; font-size: 30px; color: var(--red); line-height: 1; }
  .person__role { font-size: 13px; color: var(--white); margin-top: 2px; }
  .name-tab { position: absolute; right: 0; top: 18px; width: 22px; height: 46px; background: var(--red); }

  .address { position: absolute; left: 56px; top: 140px; font-size: 14px; line-height: 1.3; }
  .contact-list { position: absolute; left: 34px; top: 192px; list-style: none; font-size: 14px; }
  .contact-list li { display: flex; align-items: center; gap: 10px; height: 23px; white-space: nowrap; }
  .contact-list svg { width: 14px; height: 14px; fill: var(--red); flex: none; }
</style>
</head>
<body>

<section class="card card--front" aria-label="Card front">
  <div class="brand">
    <span class="brand__dot"></span>
    <span class="brand__name">MERIDIAN</span>
  </div>

  <div class="partner-row">
    <div class="ember">
      <span class="ember__mark"></span>
      <span class="ember__name">Ember steady</span>
    </div>
    <span class="cert-badge" role="img" aria-label="QJR certification badge"></span>
    <div class="distributor-strip">
      <div class="distributor-strip__own">
        <span class="brand__dot"></span>
        <span class="brand__name">MERIDIAN</span>
        <span class="distributor-strip__tag">Meridian Oil<br>Distributors</span>
      </div>
      <div class="distributor-strip__partner">
        <span class="partner-name">KESTREL</span>
        <span class="partner-sub">Premium Lubricants</span>
      </div>
    </div>
    <span class="cert-badge" role="img" aria-label="QJR certification badge"></span>
    <span class="cert-badge" role="img" aria-label="QJR certification badge"></span>
  </div>
</section>

<section class="card card--back" aria-label="Card back">
  <div class="brand">
    <span class="brand__dot"></span>
    <span class="brand__name">MERIDIAN</span>
  </div>

  <span class="ghost-brand" aria-hidden="true">MERIDIAN</span>

  <span class="name-tab"></span>
  <div class="person">
    <p class="person__name">Mara Linden</p>
    <p class="person__role">Administration Executive</p>
  </div>

  <p class="address">48 Freight Lane<br>Ashdale, WA 6109</p>

  <ul class="contact-list">
    <li><svg viewBox="0 0 16 16" aria-hidden="true"><path d="M3 1l3 3-2 2c1 2 3 4 5 5l2-2 3 3-2 3C6 14 2 10 1 3z"/></svg>1300 402 715</li>
    <li><svg viewBox="0 0 16 16" aria-hidden="true"><path d="M4 0h8v16H4zM5.5 2v10h5V2z"/></svg>+61 400 218 604</li>
    <li><svg viewBox="0 0 16 16" aria-hidden="true"><path d="M1 6h14v9H1zM4 1h8v4H4zM3 9h2v2H3zm4 0h2v2H7zm4 0h2v2h-2z"/></svg>+61 8 9400 5521</li>
    <li><svg viewBox="0 0 16 16" aria-hidden="true"><path d="M8 0a8 8 0 100 16A8 8 0 008 0zm0 2c1 1 2 3 2 6s-1 5-2 6c-1-1-2-3-2-6s1-5 2-6z"/></svg>www.meridianoil.com</li>
    <li><svg viewBox="0 0 16 16" aria-hidden="true"><path d="M0 3h16v10H0zm1.5 1.5L8 9l6.5-4.5z"/></svg>mara.linden@meridianoil.com</li>
  </ul>
</section>

</body>
</html>
```